4th Generation Family Business Needs a New Card Design!

We are a family owned 4th Generation company. We are based in the Sydney, Australia area and we are desperately in need of a more modern and classy card. We are monumental masons who design, supply & erect lasting memorials throughout cemeteries in Sydney. Our customers are normally in a period of grieving. I have attached logo files that will need to be implemented on the card. Company was established 1935. Australian Owned and Operated. Card needs to be designed to PIXO.com specification.

Target Market(s)

Our target market is based upon people that a grieving for family members that have passed away. We also deal with alot of companies that own and operate cemeteries.

Industry/Entity Type

Business

Contact Information for Business Card

Simon Harcourt, Operations Manager, 0417293086, simon@harcourtmemorials.com.au
Lewis Harcourt, Director, 0491630572, lewis@harcourtmemorials.com.au
Phone # 02 9561 3048
Website: www.harcourtmemorials.com.au
Address: Suite 17, 8 Palfrey Lane, West Carlow, Sydney NSW 2156

Font styles to use
Serif
Decorative
Script

Requirements
Must have
• Would like to see the logo nicely implemented with a modern design. Embossed lettering would be a nice additive.

```html
<!DOCTYPE html>
<html lang="en">
<head>
<meta charset="utf-8">
<title>Harcourt Memorials – Business Card</title>
<link href="https://fonts.googleapis.com/css2?family=Cinzel:wght@400;600&family=Tinos&display=swap" rel="stylesheet">
<style>
  :root {
    --backdrop: #dcdcdc;
    --card: #fbfbfb;
    --ink: #1b1b1b;
    --ink-soft: #2f2f2f;
    --gold: #d4a918;
    --gold-deep: #b78e10;
    --gold-light: #e8c64a;
    --black-band: #141414;
    --ghost: rgba(0,0,0,0.045);
  }
  * { margin: 0; padding: 0; box-sizing: border-box; }
  html, body {
    width: 1200px; height: 576px; overflow: hidden;
    background: var(--backdrop);
  }
  .stage { position: relative; width: 1200px; height: 576px; }
  .card {
    position: absolute; top: 138px; height: 294px;
    background: linear-gradient(180deg, #ffffff 0%, var(--card) 55%, #f1f1f1 100%);
    box-shadow: 0 2px 6px rgba(0,0,0,0.18);
    overflow: hidden;
  }
  .card--front { left: 80px; width: 486px; }
  .card--back { left: 602px; width: 482px; }

  .brand-name {
    font-family: "Cinzel", serif; font-weight: 400; color: var(--ink);
    text-align: center; line-height: 1.05; letter-spacing: 0.5px;
  }
  .card--front .brand-name {
    position: absolute; left: 0; right: 0; top: 108px; font-size: 34px;
  }
  .card--back .brand-name {
    position: absolute; left: 22px; width: 170px; top: 86px; font-size: 23px;
  }
  .brand-name span { display: block; }

  .front-band {
    position: absolute; left: 0; right: 0; bottom: 0; height: 10px;
    background: linear-gradient(90deg, var(--gold-deep), var(--gold-light) 50%, var(--gold-deep));
  }

  .ghost-mark {
    position: absolute; right: -40px; top: 30px; width: 200px; height: 200px;
    border: 6px solid var(--ghost);
  }

  .divider {
    position: absolute; left: 26px; top: 170px; width: 232px; height: 1px;
    background: var(--gold);
  }
  .person {
    position: absolute; right: 26px; top: 160px; text-align: right;
  }
  .person__name {
    font-family: "Cinzel", serif; font-weight: 600; font-size: 18px;
    color: var(--ink); letter-spacing: 0.3px; line-height: 1.1;
  }
  .person__role {
    font-family: "Tinos", serif; font-size: 11px; color: var(--ink-soft);
  }
  .contact-list {
    position: absolute; left: 26px; top: 192px; list-style: none;
    font-family: "Tinos", serif; font-size: 12.5px; color: var(--ink-soft);
  }
  .contact-list li { display: flex; align-items: center; height: 17.6px; }
  .contact-list svg { width: 10px; height: 10px; margin-right: 11px; fill: var(--gold); }
  .address {
    position: absolute; right: 26px; top: 208px; text-align: right;
    font-family: "Tinos", serif; font-size: 12.5px; color: var(--ink-soft); line-height: 17.6px;
  }
  .back-band { position: absolute; left: 0; bottom: 0; width: 482px; height: 28px; }
</style>
</head>
<body>
<main class="stage">
  <section class="card card--front">
    <div class="brand-name"><span>Harcourt</span><span>Memorials</span></div>
    <div class="front-band"></div>
  </section>

  <section class="card card--back">
    <div class="ghost-mark"></div>
    <div class="brand-name"><span>Harcourt</span><span>Memorials</span></div>
    <div class="divider"></div>
    <div class="person">
      <div class="person__name">SIMON HARCOURT</div>
      <div class="person__role">Operations Manager</div>
    </div>
    <ul class="contact-list">
      <li><svg viewBox="0 0 10 10"><path d="M2 0h2l1 3-1.3 1a6 6 0 0 0 2.3 2.3L7 5l3 1v2c0 1-1 2-2 2A8 8 0 0 1 0 2c0-1 1-2 2-2z"/></svg>0491630572</li>
      <li><svg viewBox="0 0 10 10"><path d="M0 3c2-2 8-2 10 0v2H7V3.5H3V5H0z M2 6h6l1 4H1z"/></svg>02 9561 3048</li>
      <li><svg viewBox="0 0 10 10"><path d="M0 2h10v1L5 6 0 3z M0 4l5 3 5-3v4H0z"/></svg>harcourtmemorials.com.au</li>
      <li><svg viewBox="0 0 10 10"><path d="M5 0a5 5 0 1 0 0 10A5 5 0 0 0 5 0zm0 1c1 1 1.5 2.5 1.5 4S6 8 5 9C4 8 3.5 6.5 3.5 5S4 2 5 1zM1 5h8v.6H1z"/></svg>lewis@harcourtmemorials.com.au</li>
    </ul>
    <div class="address">Suite 17, 8 Palfrey Lane,<br>West Carlow, Sydney NSW 2156</div>
    <svg class="back-band" viewBox="0 0 482 28" preserveAspectRatio="none">
      <defs>
        <linearGradient id="goldBand" x1="0" x2="1">
          <stop offset="0" stop-color="var(--gold-deep)"/>
          <stop offset="0.5" stop-color="var(--gold-light)"/>
          <stop offset="1" stop-color="var(--gold)"/>
        </linearGradient>
        <linearGradient id="blackBand" x1="0" x2="1">
          <stop offset="0" stop-color="#3a3a3a"/>
          <stop offset="0.4" stop-color="var(--black-band)"/>
          <stop offset="1" stop-color="#050505"/>
        </linearGradient>
      </defs>
      <rect x="0" y="17" width="260" height="11" fill="url(#goldBand)"/>
      <polygon points="258,28 278,0 482,0 482,28" fill="url(#blackBand)"/>
    </svg>
  </section>
</main>
</body>
</html>
```